Square graphic for social media post

I want to create a 1080 x 1080px all-black image for the quote below that I can share on social media. I want the emphasis to be primarily on the quote, secondarily on the portrait, and third (smallest) on the logo. I want the background on the portrait to be edited so it's transparent and just shows the face of the person on a black background (no brick wall visible).

Graphic color: black
Text color: white
Content: "What we went through is going to make the greatest generation of hoteliers our industry has ever seen." << biggest text
Derek Holm << smaller text
President, Silverbrook Hotels << smaller text
[image of person - use whichever version looks better to you]
[Add Lodging Ledger logo - whichever looks better to you]

This image needs to be readable when sized down much smaller (400x400?) so want the text and portrait to take up most of the space.

I'd like the output both as PNG and original file (preferably Canva). Thanks!

Target Market(s)

Hotel managers

Industry/Entity Type

Hospitality

Font styles to use
Sans Serif

Colors

Designer to choose colors to be used in the design.

Requirements
Must have
• Needs to focus on the quote and the person quoted (the portrait)

```html
<!DOCTYPE html>
<html lang="en">
<head>
<meta charset="utf-8">
<title>Quote Post – Derek Holm</title>
<link rel="stylesheet" href="https://fonts.googleapis.com/css2?family=Bebas+Neue&family=Outfit:wght@300;500;700;800&display=swap">
<style>
  :root {
    --bg-center: #1c1c1c;
    --bg-edge: #0b0b0b;
    --ink: #ffffff;
    --ink-dark: #111111;
    --photo-light: #5a5f6e;
    --photo-dark: #1d2a4f;
  }
  html, body {
    margin: 0;
    padding: 0;
    width: 1200px;
    height: 1200px;
    overflow: hidden;
    background: var(--bg-edge);
  }
  .quote-post {
    display: block;
    width: 1200px;
    height: 1200px;
  }
  .geo { font-family: "Outfit", sans-serif; fill: var(--ink); }
  .geo-light { font-weight: 300; }
  .geo-bold { font-weight: 800; }
  .condensed { font-family: "Bebas Neue", "Oswald", sans-serif; fill: var(--ink); }
  .band-text { font-family: "Outfit", sans-serif; font-weight: 800; fill: var(--ink-dark); }
  .brand-name { font-family: "Outfit", sans-serif; font-weight: 500; fill: var(--ink); letter-spacing: 6px; }
  .speaker-name { font-family: "Outfit", sans-serif; font-weight: 800; fill: var(--ink); }
  .speaker-role { font-family: "Outfit", sans-serif; font-weight: 300; fill: var(--ink); }
  .quote-mark { fill: none; stroke: var(--ink); stroke-width: 3; stroke-linejoin: round; }
  .accent-bar { fill: var(--ink); }
  .band { fill: var(--ink); }
  .portrait-ring { fill: none; stroke: var(--ink); stroke-width: 2; }
</style>
</head>
<body>
<svg class="quote-post" viewBox="0 0 1200 1200" xmlns="http://www.w3.org/2000/svg" aria-label="Quote by Derek Holm, President, Silverbrook Hotels">
  <defs>
    <radialGradient id="bg-glow" cx="50%" cy="40%" r="75%">
      <stop offset="0" stop-color="var(--bg-center)"/>
      <stop offset="1" stop-color="var(--bg-edge)"/>
    </radialGradient>
    <radialGradient id="portrait-fill" cx="50%" cy="40%" r="65%">
      <stop offset="0" stop-color="var(--photo-light)"/>
      <stop offset="1" stop-color="var(--photo-dark)"/>
    </radialGradient>
    <g id="quote-pair">
      <path d="M192 203 V150 C192 122 204 110 228 106 H248 V126 H236 C226 128 222 134 222 144 H246 V203 Z"/>
      <path d="M266 203 V150 C266 122 278 110 302 106 H322 V126 H310 C300 128 296 134 296 144 H320 V203 Z"/>
    </g>
  </defs>

  <rect class="background" width="1200" height="1200" fill="url(#bg-glow)"/>

  <!-- opening quotation mark -->
  <use class="quote-mark open" href="#quote-pair"/>

  <!-- publication name -->
  <g class="brand">
    <text class="brand-name" x="899" y="190" font-size="26" text-anchor="middle">LODGING LEDGER</text>
  </g>

  <!-- quote -->
  <text class="geo geo-light" x="189" y="293" font-size="76" textLength="426" lengthAdjust="spacingAndGlyphs">WHAT WE</text>
  <text class="geo geo-light" x="189" y="381" font-size="76" textLength="706" lengthAdjust="spacingAndGlyphs">WENT THROUGH IS</text>
  <text class="geo geo-bold" x="189" y="473" font-size="86" textLength="711" lengthAdjust="spacingAndGlyphs">GOING TO MAKE</text>

  <g class="accent-bars">
    <rect class="accent-bar" x="943" y="326" width="89" height="27"/>
    <rect class="accent-bar" x="943" y="386" width="89" height="27"/>
    <rect class="accent-bar" x="943" y="447" width="89" height="26"/>
  </g>

  <text class="condensed" x="189" y="640" font-size="196" textLength="841" lengthAdjust="spacingAndGlyphs">THE GREATEST</text>
  <text class="condensed" x="189" y="742" font-size="104" textLength="841" lengthAdjust="spacingAndGlyphs">GENERATION OF HOTELIERS</text>

  <rect class="band" x="189" y="773" width="841" height="65"/>
  <text class="band-text" x="232" y="824" font-size="52" textLength="757" lengthAdjust="spacingAndGlyphs">OUR INDUSTRY HAS EVER SEEN</text>

  <!-- closing quotation mark -->
  <use class="quote-mark close" href="#quote-pair" transform="translate(945 921) rotate(180) translate(-257 -154.5)"/>

  <!-- speaker -->
  <g class="speaker">
    <circle cx="277" cy="1012" r="99" fill="url(#portrait-fill)" role="img" aria-label="Portrait photo of Derek Holm on a black background"/>
    <circle class="portrait-ring" cx="277" cy="1012" r="100"/>
    <text class="speaker-name" x="417" y="1019" font-size="68" textLength="352" lengthAdjust="spacingAndGlyphs">DEREK HOLM</text>
    <text class="speaker-role" x="417" y="1065" font-size="38" textLength="540" lengthAdjust="spacingAndGlyphs">President, Silverbrook Hotels</text>
  </g>
</svg>
</body>
</html>
```